Landscape design build company door flyer

I would like this flyer to convey a high-level of professionalism for a company that is excellent with communication with their clients as well as a company that does incredible installations

Went on vacation/holiday

```html
<!DOCTYPE html>
<html lang="en">
<head>
<meta charset="utf-8">
<title>Stillwater Builders – Door Hanger</title>
<link href="https://fonts.googleapis.com/css2?family=Playfair+Display:wght@700;900&family=Lato:wght@400;700;900&display=swap" rel="stylesheet">
<style>
  :root{
    --navy:#0f3445;
    --yellow:#f7c633;
    --paper:#eeeeee;
    --paper-dark:#e2e2e2;
    --backdrop-top:#dcebfb;
    --backdrop-bottom:#bcd6f5;
    --ink:#1c2f3a;
    --rule:#c9c9c9;
  }
  *{margin:0;padding:0;box-sizing:border-box}
  html,body{width:1200px;height:669px;overflow:hidden}
  body{
    background:linear-gradient(180deg,var(--backdrop-top),var(--backdrop-bottom));
    font-family:"Lato",sans-serif;color:var(--ink);position:relative;
  }
  .hanger{
    position:absolute;top:50px;width:220px;height:569px;overflow:hidden;
    background:radial-gradient(ellipse at 50% 30%,#f4f4f4,var(--paper) 60%,var(--paper-dark));
    box-shadow:0 4px 14px rgba(30,60,100,.18);
  }
  .hanger--front{left:355px}
  .hanger--back{left:626px}

  /* front */
  .brand{
    position:absolute;top:208px;left:0;right:0;
    display:flex;align-items:center;justify-content:center;gap:6px;
    font-family:"Lato",sans-serif;font-weight:700;font-size:15px;
    color:var(--navy);letter-spacing:.4px;
  }
  .brand__mark{width:9px;height:9px;background:var(--navy)}
  .divider{position:absolute;top:235px;left:26px;right:26px;height:1px;background:var(--rule)}
  .headline{position:absolute;top:243px;left:0;right:0;text-align:center;
    font-family:"Playfair Display",serif;font-weight:900;color:var(--navy)}
  .headline__lead{font-size:15.2px;letter-spacing:-.1px;line-height:1.1}
  .headline__main{font-size:33px;line-height:1;letter-spacing:-.5px}
  .front-photo{position:absolute;left:0;right:0;top:341px;bottom:0;
    background:linear-gradient(170deg,#c9ccce 0%,#dcdedd 35%,#8fa78a 55%,#b6bdc0 75%,#eaeaea 100%)}
  .tagline{position:absolute;top:295px;left:23px;width:173px;height:31px;
    background:var(--yellow);border-radius:4px;color:var(--navy);
    font-size:10.6px;line-height:1.15;text-align:center;padding-top:3px}
  .cta-box{position:absolute;top:330px;left:54px;width:142px;height:40px;
    background:var(--navy);border-radius:4px;color:#fff;font-weight:700;
    font-size:15.5px;line-height:.98;text-align:center;padding-top:5px;letter-spacing:-.3px}

  /* back */
  .services-title{position:absolute;top:149px;left:45px;width:129px;height:30px;
    background:var(--navy);border-radius:4px;color:var(--yellow);text-align:center;
    font-family:"Playfair Display",serif;font-weight:900;font-size:21px;line-height:30px}
  .services-intro{position:absolute;top:187px;left:22px;right:22px;
    font-size:6.9px;line-height:1.25;text-align:center;color:var(--ink)}
  .service-list{position:absolute;top:258px;left:20px;right:14px;
    display:grid;grid-template-columns:1fr 1fr;row-gap:12px;column-gap:10px}
  .service-list::after{content:"";position:absolute;left:50%;top:6px;bottom:2px;width:1px;background:var(--rule)}
  .service{display:flex;align-items:center;gap:7px;font-size:9.4px;line-height:1.1;color:var(--navy)}
  .service svg{width:20px;height:20px;flex:none}
  .back-photo{position:absolute;left:0;right:0;top:364px;height:139px;
    border-top:3px solid var(--navy);
    background:linear-gradient(180deg,#7fb4e6 0%,#a9cdea 25%,#6e9561 45%,#c8ad86 65%,#e8ecef 100%)}
  .cta-band{position:absolute;left:0;right:0;top:503px;height:24px;background:var(--navy);
    color:#fff;font-weight:700;font-size:11.4px;text-align:center;line-height:24px;letter-spacing:-.1px}
  .phone-band{position:absolute;left:0;right:0;top:527px;bottom:0;background:var(--yellow);
    display:flex;align-items:center;justify-content:center;gap:8px;
    color:var(--navy);font-weight:900;font-size:19px}
  .phone-band svg{width:16px;height:16px}
</style>
</head>
<body>

<section class="hanger hanger--front">
  <div class="brand"><span class="brand__mark"></span>STILLWATER BUILDERS</div>
  <div class="divider"></div>
  <h1 class="headline">
    <div class="headline__lead">IT'S TIME TO DISCOVER</div>
    <div class="headline__main">YOUR ZEN!</div>
  </h1>
  <div class="front-photo" role="img" aria-label="Modern terrace with pergola, stepping stones over water and green plants"></div>
  <p class="tagline">From vision to reality, let us bring your dream outdoor space to life</p>
  <div class="cta-box">GET A FAST FREE ESTIMATE NOW!</div>
</section>

<section class="hanger hanger--back">
  <h2 class="services-title">SERVICES</h2>
  <p class="services-intro">Our team of skilled artisans will turn your outdoor space into a breathtaking oasis that you'll love coming home to. Whether it's a cozy patio for intimate gatherings, a sprawling deck to host memorable parties, or a custom paver driveway that adds instant curb appeal, our high-quality craftsmanship ensures stunning results that exceed your expectations.</p>
  <div class="service-list">
    <div class="service">
      <svg viewBox="0 0 20 20" fill="none" stroke="#0f3445" stroke-width="1.6"><path d="M2 14h16M2 17c3-2 5 2 8 0s5 2 8 0M6 14V8h6v6M10 4l2 4"/></svg>
      <span>Paver Patios<br>&amp; Pools</span>
    </div>
    <div class="service">
      <svg viewBox="0 0 20 20" fill="none" stroke="#0f3445" stroke-width="1.6"><path d="M2 10h16M2 17h16M5 10v7M10 10v7M15 10v7M7 3h6v5H7z"/></svg>
      <span>Decks &amp;<br>Railings</span>
    </div>
    <div class="service">
      <svg viewBox="0 0 20 20" fill="#0f3445"><rect x="2" y="3" width="4" height="4"/><rect x="8" y="3" width="4" height="4"/><rect x="14" y="3" width="4" height="4"/><rect x="5" y="9" width="4" height="4"/><rect x="11" y="9" width="4" height="4"/><rect x="2" y="15" width="4" height="4"/><rect x="8" y="15" width="4" height="4"/><rect x="14" y="15" width="4" height="4"/></svg>
      <span>Paver<br>Driveways</span>
    </div>
    <div class="service">
      <svg viewBox="0 0 20 20" fill="none" stroke="#0f3445" stroke-width="1.6"><path d="M10 3c-3 4 2 5 0 9M6 8c-2 3 0 5 4 5s6-2 4-6M3 16h14M3 18.5h14"/></svg>
      <span>Fireplace<br>&amp; Firepits</span>
    </div>
    <div class="service">
      <svg viewBox="0 0 20 20" fill="none" stroke="#0f3445" stroke-width="1.6"><path d="M2 13h16M2 17h16M7 13v4M13 13v4M10 9l7-6"/></svg>
      <span>Retaining<br>Walls</span>
    </div>
    <div class="service">
      <svg viewBox="0 0 20 20" fill="none" stroke="#0f3445" stroke-width="1.6"><path d="M7 4h6l1 7H6zM10 2v2M10 11v7M8 18h4"/></svg>
      <span>Outdoor<br>Lightning</span>
    </div>
  </div>
  <div class="back-photo" role="img" aria-label="Backyard patio with wooden pergola, lounge seating, dining set and palm trees"></div>
  <div class="cta-band">GET A FAST FREE ESTIMATE NOW!</div>
  <div class="phone-band">
    <svg viewBox="0 0 24 24" fill="#0f3445"><path d="M6.6 10.8a15.1 15.1 0 0 0 6.6 6.6l2.2-2.2c.3-.3.7-.4 1-.2 1.1.4 2.300.6 3.6.6.6 0 1 .4 1 1V20c0 .6-.4 1-1 1A17 17 0 0 1 3 4c0-.6.4-1 1-1h3.5c.6 0 1 .4 1 1 0 1.3.2 2.5.6 3.6.1.3 0 .7-.2 1z"/></svg>
    <span>555 014 2038</span>
  </div>
</section>

</body>
</html>
```